Email Signature and a letter head

I need a professional email signature and a letter head for letters sent by post. I've attached my logo and a signature i am currently using. Current letter head is also attached.

Target Market(s)

Accounting Clients

Industry/Entity Type

Public Accounting

Font styles to use
Sans Serif

Colors

Designer to choose colors to be used in the design.

Requirements
Must have
• My logo, RM Logo, Lumo Logo, Tax Agent logo. All attached.
• All my credentials - examples in the attached documents

```html
<!DOCTYPE html>
<html lang="en">
<head>
<meta charset="utf-8">
<title>Keystone Ledger Letterhead</title>
<link href="https://fonts.googleapis.com/css2?family=Open+Sans:wght@400;600;700&display=swap" rel="stylesheet">
<style>
  :root{
    --backdrop:#d9d9d9;
    --paper:#f6f6f5;
    --gold:#b38b1d;
    --ink:#2b2b2b;
    --rule:#3a3a3a;
    --watermark:#ebe6dc;
    --teal:#1b93b8;
    --badge:#8a8a8a;
  }
  *{margin:0;padding:0;box-sizing:border-box}
  html,body{width:1200px;height:780px;overflow:hidden;background:var(--backdrop);font-family:"Open Sans",Arial,sans-serif}
  .letterhead{position:absolute;left:338px;top:20px;width:523px;height:740px;background:var(--paper);box-shadow:0 2px 6px rgba(0,0,0,.12)}
  .brand{position:absolute;left:36px;top:36px;width:136px;text-align:center;color:var(--gold)}
  .brand-mark{display:block;width:48px;height:48px;margin:0 auto 5px;border:2px solid var(--gold);border-radius:50%}
  .brand-name{font-size:12px;font-weight:600;letter-spacing:.4px;line-height:1.1;white-space:nowrap}
  .brand-tag{font-size:5.5px;font-weight:600;letter-spacing:1.6px;margin-top:2px;white-space:nowrap}
  .watermark{position:absolute;left:84px;top:164px;width:360px;height:360px}
  .watermark-name{font-family:"Open Sans",Arial,sans-serif;font-weight:600;fill:var(--watermark)}
  .footer-rule{position:absolute;left:31px;top:647px;width:460px;height:1.5px;background:var(--rule)}
  .contact{position:absolute;left:31px;top:655px;color:var(--ink);font-size:7.2px;line-height:10.2px;white-space:nowrap}
  .contact-name{color:var(--gold);font-weight:700;font-size:8.8px;line-height:12px}
  .contact-line{display:flex;align-items:center;gap:4px}
  .contact-line svg{width:7px;height:7px;flex:none}
  .affiliations{position:absolute;top:665px;left:238px;width:262px;height:50px;display:flex;align-items:center;justify-content:space-between}
  .member-body{font-size:20px;font-weight:700;color:#c8373c;width:78px;text-align:center}
  .partner{display:flex;align-items:center;gap:5px;color:var(--teal);font-size:13px;font-weight:700}
  .partner-dot{width:34px;height:34px;border-radius:50%;background:var(--teal)}
  .tax-agent{display:flex;align-items:center;gap:5px;font-size:5px;line-height:6.5px;color:var(--ink);white-space:nowrap}
  .tax-badge{width:36px;height:36px;border-radius:50%;border:2px solid var(--badge);background:#eef2e4}
</style>
</head>
<body>
  <main class="letterhead">
    <header class="brand">
      <span class="brand-mark"></span>
      <div class="brand-name">KEYSTONE LEDGER</div>
      <div class="brand-tag">BUSINESS SERVICES</div>
    </header>

    <svg class="watermark" viewBox="0 0 360 360" aria-hidden="true">
      <circle cx="180" cy="180" r="175" fill="none" stroke="var(--watermark)" stroke-width="7"/>
      <text class="watermark-name" x="180" y="172" text-anchor="middle" font-size="54" textLength="270" lengthAdjust="spacingAndGlyphs">KEYSTONE</text>
      <text class="watermark-name" x="180" y="236" text-anchor="middle" font-size="54" textLength="210" lengthAdjust="spacingAndGlyphs">LEDGER</text>
    </svg>

    <div class="footer-rule"></div>

    <section class="contact">
      <div class="contact-name">Marlen Hoyt RM BBus.</div>
      <div class="contact-line">
        <svg viewBox="0 0 10 10"><path d="M5 0.5a3.3 3.3 0 0 0-3.3 3.3C1.7 6.4 5 9.5 5 9.5s3.3-3.1 3.3-5.7A3.3 3.3 0 0 0 5 .5zm0 4.6a1.3 1.3 0 1 1 0-2.6 1.3 1.3 0 0 1 0 2.6z" fill="var(--gold)"/></svg>
        17 Harlow Crescent, Bayview North VIC 3188</div>
      <div class="contact-line">
        <svg viewBox="0 0 10 10"><path d="M2.2 1l1.6 0 .8 2-1 .8a5.5 5.5 0 0 0 2.6 2.6l.8-1 2 .8V8.8c0 .4-.4.7-.8.7A8 8 0 0 1 .5 1.8c0-.4.3-.8.7-.8z" fill="var(--gold)"/></svg>
        0412555078</div>
      <div class="contact-line">
        <svg viewBox="0 0 10 10"><rect x="1" y="2" width="8" height="6" rx="1" fill="var(--gold)"/><path d="M1.5 2.6L5 5.4l3.5-2.8" stroke="#fff" stroke-width=".8" fill="none"/></svg>
        marlen@keystoneledger.com.au</div>
      <div class="contact-line">
        <svg viewBox="0 0 10 10"><circle cx="5" cy="5" r="4" fill="none" stroke="var(--gold)" stroke-width="1"/><path d="M1 5h8M5 1c-2 2.5-2 5.5 0 8M5 1c2 2.5 2 5.5 0 8" stroke="var(--gold)" stroke-width=".7" fill="none"/></svg>
        www.keystoneledger.com.au</div>
      <div>ABN: 41 902 337 615 | TAN: 278 314 06</div>
    </section>

    <section class="affiliations">
      <div class="member-body">RM</div>
      <div class="partner"><span class="partner-dot"></span>Lumo</div>
      <div class="tax-agent"><span class="tax-badge"></span><span>Tax agent<br>27831406</span></div>
    </section>
  </main>
</body>
</html>
```